Brightway Haus Inc. Business Card Design

Brightway Haus Inc. is in search of a great clean design for our business cards!

Looking to incorporate our full logo and watermark on side one (however, I am open to having the text and watermark separated within the design.)

On side two, I am looking to have contact information (Name, Position, Phone #, Email, Website (www.thebrightwayhaus.ca). Can have the logo and/or watermark as part of the design if applicable.

Please add tagline "Where Shine Counts" on either side 1 or 2. This tagline can be in a sans serif, serif or cursive font as long as it compliments overall design. Capitalization can be title or sentence case depending on how it fits within the design.

Get creative!! Looking for a clean, crisp, premium design! Looking for a glossy card finish with spot UV features when printed. Cards will also be printed with rounded corners. Standard dimensions (3.5 x 2).

Target Market(s)

B2B - primary clients are business owners or property management corporations. (residential jobs are few and far between)

Industry/Entity Type

Business

Contact Information for Business Card

- clean, crisp design
- double sided
- spot UV accents and glossy finish upon printing
- standard business card size (3.5 x 2) with rounded corners
- please see project description for requirements per side

Font styles to use
Sans Serif

Requirements
Must have
• - adequate bleeds with print ready files
• - cohesive design elements between side 1 & 2
• - spot UV elements (can be on both sides or just one, use your discretion)
• - colour pallet should match the logo file provided
• - incorporate tagline "where shine counts" (this tagline can be in a serif or sans serif font as long as it is complimentary to the overall design.
Nice to have
• - Premium elements with a clean design
Should not have
• - Please omit cartoon or whimsical like designs, think premium.
• - Colours should not stray from the pallet of the provided logo.

```html
<!DOCTYPE html>
<html lang="en">
<head>
<meta charset="utf-8">
<title>Brightway Haus Inc. Business Card</title>
<link rel="stylesheet" href="https://fonts.googleapis.com/css2?family=Open+Sans:wght@400;600;700;800&display=swap">
<style>
  :root {
    --teal: #10b9ba;
    --navy: #1b2553;
    --white: #ffffff;
    --grey: #8c8f96;
    --stage: #2b2b2b;
  }
  * { margin: 0; padding: 0; box-sizing: border-box; }
  html, body { width: 1200px; height: 960px; overflow: hidden; }
  body {
    background: var(--stage);
    font-family: "Open Sans", Arial, sans-serif;
    position: relative;
  }
  .card {
    position: absolute;
    width: 600px;
    height: 342px;
    border-radius: 22px;
    overflow: hidden;
  }
  .card-front { left: 314px; top: 113px; background: var(--teal); color: var(--white); }
  .card-back { left: 311px; top: 472px; background: var(--white); }

  .front-panel { position: absolute; inset: 0; }

  .front-brand {
    position: absolute;
    left: 30px; top: 38px;
    font-weight: 800;
    font-size: 27px;
    letter-spacing: -0.5px;
    line-height: 1;
    white-space: nowrap;
  }
  .contact { position: absolute; left: 30px; top: 121px; }
  .contact-name { font-weight: 700; font-size: 16px; line-height: 19px; }
  .contact-role { font-size: 16px; line-height: 20px; margin-bottom: 9px; }
  .contact-address { font-size: 15px; line-height: 20px; margin-bottom: 3px; }
  .contact-list { list-style: none; }
  .contact-list li {
    display: flex; align-items: center;
    font-size: 15px; line-height: 19px; height: 19px;
    white-space: nowrap;
  }
  .contact-list svg { width: 12px; height: 12px; margin-right: 11px; fill: var(--white); flex: none; }

  .back-brand {
    position: absolute;
    left: 0; right: 0; top: 142px;
    display: flex; justify-content: center; align-items: center;
    gap: 10px;
  }
  .back-brand-mark { width: 30px; height: 30px; background: var(--teal); flex: none; }
  .back-brand-name {
    font-weight: 800;
    font-size: 35px;
    line-height: 1;
    letter-spacing: -0.6px;
    color: var(--navy);
    white-space: nowrap;
  }
  .tagline {
    position: absolute;
    left: 0; right: 0; top: 192px;
    text-align: center;
    font-weight: 600;
    font-size: 13px;
    letter-spacing: 3px;
    text-transform: uppercase;
    color: var(--teal);
  }
</style>
</head>
<body>
  <section class="card card-front">
    <svg class="front-panel" width="600" height="342" viewBox="0 0 600 342" aria-hidden="true">
      <path d="M408 0 C400 90 340 150 330 240 C322 300 350 330 380 342 L600 342 L600 0 Z" fill="var(--navy)"/>
    </svg>
    <div class="front-brand">Brightway Haus Inc.</div>
    <div class="contact">
      <p class="contact-name">DANIEL REYES</p>
      <p class="contact-role">CEO/FOUNDER</p>
      <p class="contact-address">4120 Harbour View Road<br>Halifax, Nova Scotia B3H 2Y9</p>
      <ul class="contact-list">
        <li><svg viewBox="0 0 12 12"><path d="M1 4 C1 2 3 1.5 6 1.5 C9 1.5 11 2 11 4 L8.5 4.5 L8 3.5 L4 3.5 L3.5 4.5 Z M3 5 L9 5 L10.5 10.5 L1.5 10.5 Z"/></svg>902 555 0148</li>
        <li><svg viewBox="0 0 12 12"><path d="M3 0.5 H9 V11.5 H3 Z M4 1.5 V9.5 H8 V1.5 Z" fill-rule="evenodd"/></svg>902 555 0172</li>
        <li><svg viewBox="0 0 12 12"><path d="M3 0.5 H9 V4 H3 Z M1 4.5 H11 V9 H9.5 V11.5 H2.5 V9 H1 Z M3.5 8 V10.5 H8.5 V8 Z"/></svg>902 555 0193</li>
        <li><svg viewBox="0 0 12 12"><path d="M1 2.5 H11 V9.5 H1 Z M1.8 3.2 L6 6.4 L10.2 3.2 Z" fill-rule="evenodd"/></svg>hello@thebrightwayhaus.ca</li>
        <li><svg viewBox="0 0 12 12"><circle cx="6" cy="6" r="5.2"/><path d="M4 3 C5 4 5 5 4 6 C5 7 6 7 6 9 M7 2 C8 3 9 3 9.5 4" stroke="var(--teal)" stroke-width="1" fill="none"/></svg>www.thebrightwayhaus.ca</li>
      </ul>
    </div>
  </section>

  <section class="card card-back">
    <div class="back-brand">
      <span class="back-brand-mark"></span>
      <span class="back-brand-name">Brightway Haus Inc.</span>
    </div>
    <p class="tagline">Where Shine Counts</p>
  </section>
</body>
</html>
```